CM Candle Tube Packaging Design

Website: www.corvelmare.example
IG: @corvel.mare
Tagline: Elevate Your Ambiance
My brand is a sophisticated brand with luxury candles made of coconut wax. Im looking for an upscale minimalist chic design.
Discover the transformative power of positive energy with Corvel Mare candles. Indulge in true luxury with our specially crafted coconut wax blend that not only ignites captivating scents but also embodies modern elegance and empowering elements.
At Corvel Mare we're committed to delivering a unique and exhilarating aromatic experience to all candle lovers. Each candle is meticulously handcrafted in small batches using luxury fragrance oils exclusively formulated for coconut wax.
Our candles are:
Clean-burning
Paraben-Free
Phthalate-Free
Skin-Safe
Pet-Friendly

```html
<!DOCTYPE html>
<html lang="en">
<head>
<meta charset="utf-8">
<title>Corvel Mare – Candle Tube Packaging</title>
<link rel="stylesheet" href="https://fonts.googleapis.com/css2?family=Montserrat:ital,wght@0,300;0,400;0,500;1,400;1,500&family=Poiret+One&display=swap">
<style>
  :root {
    --backdrop: #f3dde6;
    --paper: #ffffff;
    --paper-shade: #f4f5f6;
    --blush: #e8aab8;
    --blush-text: #e59aac;
    --label-grey: #d9dcdf;
    --ink: #1d1d1f;
    --ink-soft: #333336;
  }
  * { margin: 0; padding: 0; box-sizing: border-box; }
  html, body { width: 1200px; height: 762px; overflow: hidden; background: var(--backdrop); }
  body { font-family: "Montserrat", sans-serif; color: var(--ink); position: relative; }

  .panel {
    position: absolute;
    top: 70px;
    width: 360px;
    height: 622px;
    background: var(--paper);
    border-radius: 6px;
    overflow: hidden;
  }
  .panel--front { left: 50px; }
  .panel--back { left: 440px; }

  .panel__lid-line {
    position: absolute; left: 0; right: 0; top: 150px;
    border-top: 1px solid #e6e7e8;
  }

  .front__sweep {
    position: absolute; top: 0; right: 0;
    width: 360px; height: 622px;
  }

  .front__label {
    position: absolute; left: 36px; top: 340px;
    width: 236px; height: 100px;
    background: var(--label-grey);
    opacity: 0.92;
    display: flex; flex-direction: column; align-items: center; justify-content: center;
  }
  .front__wordmark {
    font-family: "Poiret One", sans-serif;
    font-size: 31px; letter-spacing: 0.5px; color: var(--ink);
    white-space: nowrap;
  }
  .front__descriptor {
    margin-top: 8px;
    font-size: 8px; letter-spacing: 3.6px; font-weight: 400; color: var(--ink);
    display: flex; align-items: center; gap: 8px;
  }
  .front__descriptor::before, .front__descriptor::after {
    content: ""; width: 12px; border-top: 1px solid var(--ink);
  }
  .front__tagline {
    position: absolute; left: 86px; top: 520px;
    font-style: italic; font-weight: 500; font-size: 13px;
  }
  .front__weight {
    position: absolute; left: 128px; top: 580px;
    font-size: 10px; font-weight: 400;
  }

  .panel__monogram {
    position: absolute; top: 50px; left: 0; right: 0; text-align: center;
    font-family: "Poiret One", sans-serif; font-size: 30px; color: var(--ink);
  }

  .back__sliver { position: absolute; left: 0; top: 0; width: 30px; height: 622px; }
  .back__copy {
    position: absolute; left: 50px; right: 50px; top: 270px;
    text-align: center; font-size: 7.4px; line-height: 1.45; font-weight: 400; color: var(--ink-soft);
  }
  .back__copy p + p, .back__copy ul + p { margin-top: 7px; }
  .back__claims {
    list-style: none; display: flex; justify-content: center; gap: 9px; margin-top: 7px;
  }
  .back__claims li::before { content: "•"; margin-right: 2px; }

  .back__values {
    position: absolute; left: 44px; right: 44px; top: 440px;
    display: flex; justify-content: space-between; list-style: none;
  }
  .value { width: 46px; text-align: center; }
  .value__icon {
    display: block; width: 22px; height: 22px; margin: 0 auto 6px;
    border-radius: 50%; background: #f6d3dc;
  }
  .value__name {
    font-size: 6.6px; line-height: 1.3; color: var(--blush-text); letter-spacing: 0.3px;
  }

  .back__signoff {
    position: absolute; left: 0; right: 0; top: 530px; text-align: center;
    font-size: 7.6px; color: var(--ink-soft);
  }
  .back__signoff em { font-weight: 500; display: block; margin-bottom: 10px; }

  .lid {
    position: absolute; left: 860px; top: 235px;
    width: 292px; height: 292px; border-radius: 50%;
    background: var(--paper);
    box-shadow: inset 0 0 0 12px var(--paper-shade);
    display: flex; align-items: center; justify-content: center;
  }
  .lid__monogram {
    font-family: "Poiret One", sans-serif; font-size: 64px; color: var(--ink);
  }
</style>
</head>
<body>

  <section class="panel panel--front" aria-label="Front of tube">
    <div class="panel__monogram">CM</div>
    <div class="panel__lid-line"></div>
    <svg class="front__sweep" viewBox="0 0 360 622" role="img" aria-label="Large blush flame-shaped decorative sweep">
      <path d="M360 0 L360 622 L150 622 C150 520 170 420 210 330 C260 220 320 120 360 0 Z" fill="var(--blush)"/>
    </svg>
    <div class="front__label">
      <div class="front__wordmark">CORVEL MARE</div>
      <div class="front__descriptor">HANDMADE CANDLES</div>
    </div>
    <p class="front__tagline">Elevate Your Ambiance</p>
    <p class="front__weight">14OZ / 396G</p>
  </section>

  <section class="panel panel--back" aria-label="Back of tube">
    <div class="panel__monogram">CM</div>
    <div class="panel__lid-line"></div>
    <svg class="back__sliver" viewBox="0 0 30 622" aria-hidden="true">
      <path d="M0 380 C14 440 18 540 6 622 L0 622 Z" fill="var(--blush)"/>
    </svg>
    <div class="back__copy">
      <p>At Corvel Mare, we believe that positive energy can move mountains. We strive to elevate that energy in every way possible. Our coconut wax combination creates an enticing scent with no compromises modern, classy aromas with empowering elements.</p>
      <p>We believe that candle lovers deserve only the best. Our candles are made from luxury fragrance oil specially formulated for coconut wax and are:</p>
      <ul class="back__claims">
        <li>Clean</li><li>Paraben Free</li><li>Skin Safe</li><li>Pet Friendly</li>
      </ul>
      <p>Nothing says luxury and class quite like being able to create your own perfect scent in the comfort of your own home.</p>
    </div>
    <ul class="back__values">
      <li class="value"><span class="value__icon" role="img" aria-label="Line icon of hands pouring"></span><span class="value__name">HAND<br>POURED</span></li>
      <li class="value"><span class="value__icon" role="img" aria-label="Line icon of a leafy bowl"></span><span class="value__name">VEGAN</span></li>
      <li class="value"><span class="value__icon" role="img" aria-label="Line icon of a paw print"></span><span class="value__name">PET<br>FRIENDLY</span></li>
      <li class="value"><span class="value__icon" role="img" aria-label="Line icon of flowers"></span><span class="value__name">UNIQUELY<br>SCENTED</span></li>
      <li class="value"><span class="value__icon" role="img" aria-label="Line icon representing a woman-owned business"></span><span class="value__name">LATINA<br>WOMAN<br>OWNED</span></li>
    </ul>
    <div class="back__signoff">
      <em>Made with love in small batches.</em>
      <div>www.corvelmare.example</div>
      <div>@corvel.mare</div>
    </div>
  </section>

  <section class="lid" aria-label="Tube lid">
    <span class="lid__monogram">CM</span>
  </section>

</body>
</html>
```